Corvane Freight Company Business Card Design

We are a company that delivers natural saltwater (from the ocean) to aquarium companies, restaurants and home marine tanks. I would like a new business card to suit.

Must include Name, company name, abn, contact number and website as well as logo (see attached).

Looking for a design that stands out, has a clean but unique appearance.

Double and single sided entries welcome

Business

• Logo

```html
<!DOCTYPE html>
<html lang="en">
<head>
<meta charset="utf-8">
<title>Corvane Freight Company – Business Card</title>
<link rel="stylesheet" href="https://fonts.googleapis.com/css2?family=Source+Sans+3:wght@400;600&display=swap">
<style>
  :root {
    --backdrop: #2e2521;
    --card-white: #ffffff;
    --brand-blue: #0b5aa9;
    --sky-blue: #4cc6f0;
    --logo-blue: #2aa3dc;
    --name-blue: #1d6db4;
    --body-grey: #4a4a4a;
    --divider: #bdbdbd;
  }
  * { box-sizing: border-box; margin: 0; padding: 0; }
  html, body {
    width: 1200px; height: 471px; overflow: hidden;
    background: var(--backdrop);
    font-family: "Source Sans 3", "Myriad Pro", Arial, sans-serif;
  }
  .canvas { position: relative; width: 1200px; height: 471px; }

  .card {
    position: absolute; top: 73px;
    width: 522px; height: 299px;
    border-radius: 22px; overflow: hidden;
  }
  .card--front { left: 47px; background: var(--card-white); }
  .card--back {
    left: 606px; background: var(--brand-blue);
    border: 1px solid #d7dde4;
  }

  .edge-band { position: absolute; top: 0; right: 0; width: 32px; height: 100%; }

  .front-logo {
    position: absolute; left: 22px; top: 180px; width: 270px;
    text-align: center; color: var(--logo-blue);
    font-size: 33px; font-weight: 400; line-height: 1;
  }
  .front-logo span { display: block; font-size: 21px; margin-top: 4px; }

  .divider {
    position: absolute; left: 292px; top: 66px; width: 1px; height: 176px;
    background: linear-gradient(to bottom, rgba(189,189,189,0), var(--divider) 25%, var(--divider) 75%, rgba(189,189,189,0));
  }

  .contact { position: absolute; left: 322px; top: 62px; color: var(--body-grey); }
  .contact__name { color: var(--name-blue); font-size: 20px; line-height: 24px; }
  .contact__title { color: var(--name-blue); font-size: 15px; line-height: 20px; }
  .contact__line {
    display: flex; align-items: center; gap: 7px;
    font-size: 13.5px; line-height: 22px;
  }
  .contact__line svg { width: 9px; height: 9px; }
  .contact__lines { margin-top: 14px; }
  .contact__address { margin-top: 12px; font-size: 13.5px; line-height: 19px; }
  .contact__abn { margin-top: 11px; font-size: 13.5px; letter-spacing: 0.3px; }

  .back-logo {
    position: absolute; left: 0; right: 0; top: 118px;
    text-align: center; color: #ffffff;
    font-size: 58px; font-weight: 400; line-height: 1;
  }
  .back-logo span { display: block; font-size: 30px; margin-top: 6px; }
</style>
</head>
<body>
<main class="canvas">

  <section class="card card--front" aria-label="Card front">
    <svg class="edge-band" viewBox="0 0 32 299" preserveAspectRatio="none" aria-hidden="true">
      <rect width="32" height="299" fill="var(--brand-blue)"/>
      <polygon points="0,0 32,0 32,100 0,132" fill="var(--sky-blue)"/>
    </svg>

    <div class="front-logo">Corvane Freight<span>Company</span></div>

    <div class="divider"></div>

    <div class="contact">
      <div class="contact__name">Your Name</div>
      <div class="contact__title">Title</div>
      <div class="contact__lines">
        <div class="contact__line">
          <svg viewBox="0 0 10 10" aria-hidden="true"><path d="M2 0.5 L3.6 2.6 L2.6 3.6 Q3.8 6 6.4 7.4 L7.4 6.4 L9.5 8 L8.2 9.5 Q2.5 8 0.5 1.8 Z" fill="#555"/></svg>
          123-456-7892
        </div>
        <div class="contact__line">
          <svg viewBox="0 0 10 10" aria-hidden="true"><circle cx="5" cy="5" r="4.3" fill="none" stroke="#555" stroke-width="1.2"/><path d="M0.8 5 H9.2 M5 0.8 Q2.5 5 5 9.2 M5 0.8 Q7.5 5 5 9.2" fill="none" stroke="#555" stroke-width="0.9"/></svg>
          www.corvanefreight.com
        </div>
      </div>
      <div class="contact__address">Street Name, City Name<br>State, Zip Code</div>
      <div class="contact__abn">ABN: 123456789</div>
    </div>
  </section>

  <section class="card card--back" aria-label="Card back">
    <div class="back-logo">Corvane Freight<span>Company</span></div>
  </section>

</main>
</body>
</html>
```